Kelvor Engineers: Why you should hire us keepsake

New design. Open to plastic cards. We are an engineering firm that designs cell phone towers and commercial buildings. Please check out our website www.kelvorstruct.com for more details. We want people to remember our card and for it to be useful if possible. We want the same look and feel on these cards to be translated to other marketing material we may need such as brochures.

Target Market(s)

Architects, Developers and Telecommunication Carriers

Industry/Entity Type

Engineering

Contact Information for Business Card

Card with our company colors, logo, and innovative design with elements related to our industry.

Font styles to use
Sans Serif

Colors
9bcb3c
abd036
0255a3

Requirements
Must have
• Sleek and hip design
Nice to have
• Bright lime green and navy coloring that pops with an innovative design.
Should not have
• A basic and boring design

```html
<!DOCTYPE html>
<html lang="en">
<head>
<meta charset="utf-8">
<title>Kelvor Engineers – Business Card</title>
<link rel="stylesheet" href="https://fonts.googleapis.com/css2?family=Roboto:wght@400;500;700;900&display=swap">
<style>
  :root{
    --navy:#1c3160;
    --lime:#cdd629;
    --white:#ffffff;
    --backdrop:#e4e5e8;
    --ink:#1c3160;
  }
  *{box-sizing:border-box;margin:0;padding:0}
  html,body{width:1200px;height:900px;overflow:hidden}
  body{background:var(--backdrop);font-family:"Roboto",Arial,sans-serif;position:relative}

  .card{position:absolute;width:560px;height:320px;border-radius:18px;overflow:hidden;
        box-shadow:0 10px 28px rgba(20,30,60,.22)}
  .card--back{left:320px;top:110px;background:var(--navy)}
  .card--front{left:320px;top:470px;background:var(--white)}

  /* back side */
  .back-brand{position:absolute;left:0;right:0;top:92px;text-align:center;
              font-weight:900;font-size:104px;line-height:1;color:var(--lime);letter-spacing:-2px}
  .back-tagline{position:absolute;left:0;right:0;top:228px;text-align:center;
                color:var(--white);font-weight:500;font-size:15px;letter-spacing:2.5px}

  /* front side */
  .front-art{position:absolute;inset:0}
  .front-brand{position:absolute;left:34px;top:18px;font-weight:900;font-size:50px;
               line-height:1;color:var(--lime);letter-spacing:-1px}
  .person{position:absolute;left:36px;top:78px}
  .person__name{font-weight:700;font-size:18px;line-height:22px;color:var(--ink)}
  .person__title{font-weight:400;font-size:12.5px;line-height:15px;color:var(--lime)}
  .person__rule{width:70px;height:1.5px;background:var(--ink);margin:6px 0 7px}
  .contacts{list-style:none}
  .contacts li{display:flex;align-items:center;gap:9px;font-size:13px;color:var(--ink);line-height:16px}
  .contacts svg{width:10px;height:10px;flex:none}
  .offices{position:absolute;right:40px;top:244px;text-align:right;color:var(--white);
           font-weight:500;font-size:14px;letter-spacing:2px;line-height:15.5px}
</style>
</head>
<body>

<section class="card card--back" aria-label="Card back">
  <div class="back-brand">Kelvor</div>
  <div class="back-tagline">MULTI-DISCIPLINE ENGINEERING</div>
</section>

<section class="card card--front" aria-label="Card front">
  <svg class="front-art" viewBox="0 0 560 320" preserveAspectRatio="none" aria-hidden="true">
    <path d="M0,200 Q150,300 560,160 L560,320 L0,320 Z" fill="var(--lime)"/>
    <path d="M0,216 Q150,316 560,176 L560,320 L0,320 Z" fill="var(--white)"/>
    <path d="M0,220 Q150,320 560,180 L560,320 L0,320 Z" fill="var(--navy)"/>
  </svg>

  <div class="front-brand">Kelvor</div>

  <div class="person">
    <div class="person__name">Dana Ellery Voss</div>
    <div class="person__title">Director</div>
    <div class="person__rule"></div>
    <ul class="contacts">
      <li><svg viewBox="0 0 10 10"><path d="M2 1 L4 3 L3 4 Q4 6 6 7 L7 6 L9 8 L8 9 Q3 9 1 2 Z" fill="var(--lime)"/></svg>404.555.0182</li>
      <li><svg viewBox="0 0 10 10"><rect x="2.5" y="0.5" width="5" height="9" rx="1" fill="none" stroke="var(--lime)" stroke-width="1.2"/></svg>706.555.0147</li>
      <li><svg viewBox="0 0 10 10"><rect x="0.6" y="2" width="8.8" height="6" fill="none" stroke="var(--lime)" stroke-width="1.1"/><path d="M0.6 2 L5 5.5 L9.4 2" fill="none" stroke="var(--lime)" stroke-width="1.1"/></svg>dvoss@kelvorstruct.com</li>
      <li><svg viewBox="0 0 10 10"><circle cx="5" cy="5" r="4.3" fill="none" stroke="var(--lime)" stroke-width="1.1"/><path d="M0.7 5 H9.3 M5 0.7 Q2.5 5 5 9.3 M5 0.7 Q7.5 5 5 9.3" fill="none" stroke="var(--lime)" stroke-width="0.9"/></svg>www.kelvorstruct.com</li>
    </ul>
  </div>

  <div class="offices">ATLANTA<br>CHARLOTTE<br>HOUSTON<br>SAN ANTONIO</div>
</section>

</body>
</html>
```